A start up Private Wine Label for export to Asia.

We are looking for the best graphic design for our very first wine label Corvessa Wines and would like the following requirements:

1. Black background - explore and play around the shade of black
2. Gold Shimmery Colour Font
3. Font should be a cursive classic posh that says Corvessa Wines
4. We would like the front graphic design to be simple and elegant and has a traditional classic feel to it.

Target Market(s)

Small scale to test the upper class market for export to Asia

Font styles to use
Script

Colors

Designer to choose colors to be used in the design.

Requirements
Must have
• Gold font for the label Corvessa Wines with shimmery touch to it.
• Elegant black background.
• Simple but elegant design.
• Attractive to the upper class market in Asia.
Nice to have
• Explore and play around with your imagination.

```html
<!DOCTYPE html>
<html lang="en">
<head>
<meta charset="utf-8">
<title>Corvessa Wines – Label</title>
<link rel="stylesheet" href="https://fonts.googleapis.com/css2?family=Pinyon+Script&display=swap">
<style>
  :root {
    --page: #ffffff;
    --label-centre: #26282e;
    --label-mid: #1b1c21;
    --label-edge: #0d0e12;
    --gold: #d9a762;
    --ornament-gold: rgba(222, 170, 98, 0.62);
    --ornament-gold-soft: rgba(200, 148, 80, 0.28);
    --ornament-faint: rgba(130, 100, 66, 0.13);
  }
  * { box-sizing: border-box; margin: 0; padding: 0; }
  html, body {
    width: 1200px;
    height: 1200px;
    overflow: hidden;
    background: var(--page);
  }
  .canvas {
    position: relative;
    width: 1200px;
    height: 1200px;
  }
  .wine-label {
    position: absolute;
    left: 238px;
    top: 238px;
    width: 724px;
    height: 724px;
    overflow: hidden;
    background: radial-gradient(ellipse at 50% 42%, var(--label-centre) 0%, var(--label-mid) 58%, var(--label-edge) 100%);
  }
  .ornament {
    position: absolute;
  }
  .ornament--top {
    left: 40px;
    top: 0;
    width: 644px;
    height: 190px;
    background: radial-gradient(ellipse 50% 100% at 50% 0%,
      var(--ornament-gold) 0%,
      var(--ornament-gold-soft) 55%,
      rgba(200, 148, 80, 0) 100%);
  }
  .ornament--bottom {
    left: 40px;
    bottom: 0;
    width: 644px;
    height: 190px;
    background: radial-gradient(ellipse 50% 100% at 50% 100%,
      var(--ornament-gold) 0%,
      var(--ornament-gold-soft) 55%,
      rgba(200, 148, 80, 0) 100%);
  }
  .ornament--left,
  .ornament--right {
    top: 50px;
    width: 200px;
    height: 620px;
  }
  .ornament--left {
    left: 0;
    background: radial-gradient(ellipse 100% 50% at 0% 50%,
      var(--ornament-faint) 0%,
      rgba(130, 100, 66, 0.06) 60%,
      rgba(130, 100, 66, 0) 100%);
  }
  .ornament--right {
    right: 0;
    background: radial-gradient(ellipse 100% 50% at 100% 50%,
      var(--ornament-faint) 0%,
      rgba(130, 100, 66, 0.06) 60%,
      rgba(130, 100, 66, 0) 100%);
  }
  .brand {
    position: absolute;
    inset: 0;
    font-family: "Pinyon Script", cursive;
    font-weight: 400;
    color: var(--gold);
  }
  .brand-name,
  .brand-type {
    position: absolute;
    left: 0;
    right: 0;
    text-align: center;
    line-height: 1.2;
    white-space: nowrap;
  }
  .brand-name {
    top: 251px;
    font-size: 160px;
    letter-spacing: 1px;
  }
  .brand-type {
    top: 441px;
    font-size: 90px;
  }
</style>
</head>
<body>
  <main class="canvas">
    <section class="wine-label">
      <div class="ornament ornament--left" role="img" aria-label="Faint mandala ornament on the left edge"></div>
      <div class="ornament ornament--right" role="img" aria-label="Faint mandala ornament on the right edge"></div>
      <div class="ornament ornament--top" role="img" aria-label="Gold mandala ornament along the top edge"></div>
      <div class="ornament ornament--bottom" role="img" aria-label="Gold mandala ornament along the bottom edge"></div>
      <h1 class="brand">
        <span class="brand-name">Corvessa</span>
        <span class="brand-type">Wines</span>
      </h1>
    </section>
  </main>
</body>
</html>
```